Business Card Design Project

Business Card
We are rebranding with a new logo
Industry/Entity Type
Business
Contact Information for Business Card
Dennis Morvale +61 487215963 dennis@quorv.com.au P.O. Box 872 Fernlow QLD 4309
Requirements
Must have
- Logo

```html
<!DOCTYPE html>
<html lang="en">
<head>
<meta charset="utf-8">
<title>Quorv International – Business Card</title>
<link href="https://fonts.googleapis.com/css2?family=Arimo:wght@400;700&display=swap" rel="stylesheet">
<style>
  :root {
    --backdrop: #2a2d31;
    --card: #ffffff;
    --brand-blue: #1590c9;
    --deep-blue: #0b6fa6;
    --light-blue: #3fb0e0;
    --brand-orange: #f28a1e;
    --warm-orange: #f7a733;
    --ink: #333a40;
    --muted: #555c63;
  }
  * { box-sizing: border-box; margin: 0; padding: 0; }
  html, body {
    width: 1200px; height: 902px; overflow: hidden;
    background: var(--backdrop);
    font-family: "Arimo", Arial, sans-serif;
  }
  .card {
    position: absolute; left: 150px; top: 194px;
    width: 900px; height: 514px;
    background: var(--card);
    border-radius: 28px;
    overflow: hidden;
    box-shadow: 0 20px 50px rgba(0,0,0,.45);
  }
  .card-art { position: absolute; inset: 0; }
  .brand {
    position: absolute; right: 70px; top: 60px;
    display: flex; align-items: center; gap: 14px;
    color: var(--brand-blue);
    font-weight: 700; font-size: 34px; letter-spacing: 1px;
  }
  .brand-dot {
    width: 22px; height: 22px; border-radius: 50%;
    background: var(--brand-orange);
  }
  .edge-tab {
    position: absolute; right: -10px; top: 180px;
    width: 24px; height: 40px; border-radius: 8px;
    background: var(--brand-blue);
  }
  .holder { position: absolute; right: 60px; top: 200px; text-align: right; }
  .holder-name { color: var(--brand-blue); font-weight: 700; font-size: 36px; }
  .holder-role { color: var(--muted); font-size: 17px; margin-top: 6px; }
  .contact { position: absolute; left: 360px; top: 300px; color: var(--ink); font-size: 24px; line-height: 1.3; }
  .contact-row { display: flex; align-items: flex-start; gap: 16px; }
  .contact-row + .contact-row { margin-top: 6px; }
  .contact-row.spaced { margin-top: 26px; }
  .contact-icon { width: 20px; height: 20px; margin-top: 5px; fill: var(--brand-blue); flex: none; }
</style>
</head>
<body>
  <main class="card">
    <svg class="card-art" viewBox="0 0 900 514" aria-hidden="true">
      <defs>
        <linearGradient id="sweep-blue" x1="0" y1="0" x2="1" y2="0">
          <stop offset="0" stop-color="var(--deep-blue)"/>
          <stop offset="1" stop-color="var(--light-blue)"/>
        </linearGradient>
        <radialGradient id="sweep-orange" cx=".5" cy=".5" r=".5">
          <stop offset="0" stop-color="var(--warm-orange)"/>
          <stop offset="1" stop-color="var(--brand-orange)"/>
        </radialGradient>
        <clipPath id="sweep-clip">
          <path d="M0 0 H360 C250 120 190 300 170 514 H0 Z"/>
        </clipPath>
      </defs>
      <path d="M0 0 H360 C250 120 190 300 170 514 H0 Z" fill="url(#sweep-blue)"/>
      <g clip-path="url(#sweep-clip)">
        <ellipse cx="60" cy="390" rx="150" ry="200" fill="url(#sweep-orange)"/>
        <path d="M300 0 H360 C250 120 190 300 170 514 H130 C160 300 210 120 300 0 Z" fill="var(--brand-blue)" opacity=".6"/>
      </g>
    </svg>

    <div class="brand"><span class="brand-dot"></span>QUORV INTERNATIONAL</div>
    <div class="edge-tab"></div>

    <div class="holder">
      <p class="holder-name">Dennis Morvale</p>
      <p class="holder-role">Owner</p>
    </div>

    <div class="contact">
      <div class="contact-row">
        <svg class="contact-icon" viewBox="0 0 20 20"><path d="M10 2 1 10h3v8h4v-5h4v5h4v-8h3z"/></svg>
        <p>P.O. Box 872<br>Fernlow QLD 4309</p>
      </div>
      <div class="contact-row spaced">
        <svg class="contact-icon" viewBox="0 0 20 20"><path d="M6 1h8a1 1 0 0 1 1 1v16a1 1 0 0 1-1 1H6a1 1 0 0 1-1-1V2a1 1 0 0 1 1-1zm1 2v12h6V3zm3 13a1 1 0 1 0 0 2 1 1 0 0 0 0-2z"/></svg>
        <p>+61 487215963</p>
      </div>
      <div class="contact-row">
        <svg class="contact-icon" viewBox="0 0 20 20"><path d="M1 4h18v12H1zm2 2v.4l7 5 7-5V6l-7 5z"/></svg>
        <p>dennis@quorv.com.au</p>
      </div>
    </div>
  </main>
</body>
</html>
```